Software allocation system needs a business card design

We need a business card designed for our software platform - www.tallivo.com.au

At the moment the logo and website is all black and white, we are happy for suggestions on implementing some colour throughout either the logo or business card.

Industry/Entity Type

Software

Font styles to use
Sans Serif

Colors

Designer to choose colors to be used in the design.

```html
<!DOCTYPE html>
<html lang="en">
<head>
<meta charset="utf-8">
<title>Tallivo – Business Card</title>
<link rel="stylesheet" href="https://fonts.googleapis.com/css2?family=Josefin+Sans:wght@300&family=Open+Sans:wght@400;600;700&display=swap">
<style>
  :root{
    --page:#3b3b3b;
    --card:#f7f7f7;
    --ink:#1e1e1e;
    --ink-soft:#333333;
    --accent:#4fb8ea;
    --band-grey:#c4c4c4;
    --rule:#9a9a9a;
  }
  *{box-sizing:border-box;margin:0;padding:0}
  html,body{width:1200px;height:749px;overflow:hidden}
  body{background:var(--page);font-family:"Open Sans",Arial,sans-serif;color:var(--ink)}
  .card{position:absolute;left:120px;top:95px;width:960px;height:560px;background:var(--card);overflow:hidden}
  .card-bands{position:absolute;inset:0;width:960px;height:560px}
  .brand{position:absolute;left:0;right:0;top:72px;display:flex;justify-content:center;align-items:center;gap:18px}
  .brand-dot{width:22px;height:22px;border-radius:50%;background:var(--accent)}
  .brand-name{font-family:"Josefin Sans","Open Sans",sans-serif;font-weight:300;font-size:62px;letter-spacing:12px;color:var(--ink);line-height:1}
  .tagline{position:absolute;left:0;right:0;top:174px;text-align:center;font-size:25px;font-weight:400;color:var(--ink-soft);letter-spacing:-.3px}
  .divider{position:absolute;left:484px;top:280px;width:2px;height:200px;background:var(--rule)}
  .contact{position:absolute;display:flex;align-items:center;gap:12px;font-size:17px;line-height:1.25;color:var(--ink)}
  .contact svg{width:22px;height:22px;flex:none;fill:var(--ink-soft)}
  .address{left:82px;top:300px;align-items:flex-start}
  .address svg{margin-top:4px}
  .phone-1{left:84px;top:364px}
  .phone-2{left:84px;top:392px}
  .phone-3{left:84px;top:420px}
  .email{left:628px;top:376px}
  .web{left:628px;top:410px}
  .person{position:absolute;left:574px;width:300px;top:274px;text-align:center}
  .person-name{font-size:29px;font-weight:700;line-height:1.1;color:var(--ink)}
  .person-name .surname{color:var(--accent)}
  .person-role{font-size:26px;font-weight:400;line-height:1.1;color:var(--ink)}
</style>
</head>
<body>
<main class="card">
  <svg class="card-bands" viewBox="0 0 960 560" aria-hidden="true">
    <polygon points="176,0 784,0 776,8 184,8" fill="var(--accent)"/>
    <polygon points="0,536 616,536 600,550 0,550" fill="var(--band-grey)"/>
    <polygon points="636,512 960,512 960,560 614,560" fill="var(--accent)"/>
  </svg>

  <div class="brand">
    <span class="brand-dot"></span>
    <span class="brand-name">TALLIVO</span>
  </div>
  <p class="tagline">PLANNING &amp; COMPLIANCE FOR HEAVY INDUSTRY</p>

  <div class="contact address">
    <svg viewBox="0 0 24 24"><path d="M12 2a7 7 0 0 0-7 7c0 5 7 13 7 13s7-8 7-13a7 7 0 0 0-7-7zm0 9.5A2.5 2.5 0 1 1 12 6.5a2.5 2.5 0 0 1 0 5z"/></svg>
    <span>PO Box 216<br>Kelby Park NSW 2071</span>
  </div>
  <div class="contact phone-1">
    <svg viewBox="0 0 24 24"><path d="M2 9c0-3 4-5 10-5s10 2 10 5v2h-5V9c-1-1-3-1-5-1s-4 0-5 1v2H2z"/><path d="M5 13h14l1 7H4z"/></svg>
    <span>02 5550 1184</span>
  </div>
  <div class="contact phone-2">
    <svg viewBox="0 0 24 24"><path d="M7 2h8l2 2v5H7z"/><path d="M3 10h18v10H3zm3 3v2h3v-2zm0 3v2h3v-2zm5-3v2h3v-2zm0 3v2h3v-2z"/></svg>
    <span>02 5550 1185</span>
  </div>
  <div class="contact phone-3">
    <svg viewBox="0 0 24 24"><path d="M7 1h10a1 1 0 0 1 1 1v20a1 1 0 0 1-1 1H7a1 1 0 0 1-1-1V2a1 1 0 0 1 1-1zm1 3v14h8V4zm4 15.5a1 1 0 1 0 0 2 1 1 0 0 0 0-2z"/></svg>
    <span>0455 501 372</span>
  </div>

  <div class="divider"></div>

  <div class="person">
    <p class="person-name">Lena <span class="surname">Marsh</span></p>
    <p class="person-role">Job title here</p>
  </div>

  <div class="contact email">
    <svg viewBox="0 0 24 24"><path d="M2 5h20v14H2zm2 2v.5l8 6 8-6V7zm0 3v7h16v-7l-8 6z"/></svg>
    <span>hello@tallivo.com.au</span>
  </div>
  <div class="contact web">
    <svg viewBox="0 0 24 24"><path d="M4 4h16v11H4zm2 2v7h12V6zM1 17h22l-2 3H3z"/></svg>
    <span>www.tallivo.com.au</span>
  </div>
</main>
</body>
</html>
```